Business Card Design Project

This is the first time we use our new logo. We need a business card that we can use both on our institutional corporate relationships and also that works for our staff that deals with consumers directly.

VELUNDA is a new company dedicated to empower consumers and to provide them with the best choices for specialized health care using the latest telemedicine technology (medicine at a distance via videoconference).

We want to print this cards in high quality materials and process. We will like designs that allow us to use UV spot varnish and other techniques that will differentiate us.

We are including Two different versions of Color logos. In addition we are including white over black background logos. Those can be used replacing the black for a color.

Please note this is the first time we will be creating any corporate materials with our new logo and colors.

Target Market(s)

34+ consumers of medium high and high socioeconomic levels.

Industry/Entity Type

Health

Requirements
Must have
• Our logo on its original colors
Should not have
• Any other graphical element or design that is not our logo

```html
<!DOCTYPE html>
<html lang="en">
<head>
<meta charset="utf-8">
<title>Velunda Business Card</title>
<link rel="stylesheet" href="https://fonts.googleapis.com/css2?family=Poppins:wght@400;600&family=Arimo:wght@400&display=swap">
<style>
  :root {
    --page: #e9ebef;
    --navy: #17557f;
    --sky: #58b4dc;
    --line-blue: #5fb8e2;
    --teal: #17a99a;
    --white: #ffffff;
    --ink-light: #ffffff;
  }
  * { box-sizing: border-box; margin: 0; padding: 0; }
  html, body {
    width: 1200px; height: 987px; overflow: hidden;
    background: var(--page);
  }
  .canvas { position: relative; width: 1200px; height: 987px; }

  .card {
    position: absolute;
    width: 640px; height: 366px;
    border-radius: 30px;
    overflow: hidden;
    box-shadow: 0 10px 28px rgba(40, 60, 90, 0.18);
  }

  /* Back of card */
  .card-back {
    left: 520px; top: 70px;
    background: var(--sky);
    display: flex; flex-direction: column;
    align-items: center; justify-content: center;
    gap: 22px;
  }
  .back-brand {
    display: flex; align-items: center; gap: 16px;
    color: var(--white);
    font-family: "Poppins", sans-serif; font-weight: 600;
    font-size: 58px; letter-spacing: 4px; line-height: 1;
  }
  .back-brand .mark-dot {
    width: 38px; height: 38px; border-radius: 50%;
    background: var(--white);
  }
  .back-url {
    color: var(--white);
    font-family: "Arimo", sans-serif; font-size: 20px;
    letter-spacing: 6px;
  }

  /* Front of card */
  .card-front {
    left: 50px; top: 540px;
    background: var(--white);
  }
  .card-front .band { position: absolute; inset: 0; }

  .front-brand {
    position: absolute; left: 56px; top: 48px;
    display: flex; align-items: center; gap: 16px;
    color: var(--navy);
    font-family: "Poppins", sans-serif; font-weight: 600;
    font-size: 60px; letter-spacing: 4px; line-height: 1;
  }
  .front-brand .mark-dot {
    width: 40px; height: 40px; border-radius: 50%;
    background: var(--teal);
  }

  .person {
    position: absolute; right: 40px; top: 138px;
    font-family: "Arimo", sans-serif; font-size: 24px;
    color: var(--navy); font-weight: 400;
  }
  .person .name { font-weight: 700; }
  .person .title { color: var(--teal); }

  .address {
    position: absolute; left: 24px; top: 208px; width: 170px;
    text-align: right;
    font-family: "Arimo", sans-serif; font-size: 17px; line-height: 1.4;
    color: var(--ink-light);
  }
  .divider {
    position: absolute; left: 210px; top: 206px;
    width: 1px; height: 120px; background: rgba(255,255,255,0.75);
  }
  .contacts {
    position: absolute; left: 226px; top: 222px;
    list-style: none;
    font-family: "Arimo", sans-serif; font-size: 17px; line-height: 1.5;
    color: var(--ink-light);
  }
  .contacts li { display: flex; align-items: center; gap: 8px; }
  .contacts svg { width: 14px; height: 14px; flex: none; }
</style>
</head>
<body>
<main class="canvas">

  <section class="card card-back" aria-label="Card back">
    <div class="back-brand"><span class="mark-dot"></span><span>VELUNDA</span></div>
    <p class="back-url">www.velunda.com</p>
  </section>

  <section class="card card-front" aria-label="Card front">
    <svg class="band" viewBox="0 0 640 366" preserveAspectRatio="none" aria-hidden="true">
      <path d="M0,108 Q 480,118 625,366" fill="none" stroke="var(--line-blue)" stroke-width="3"/>
      <path d="M0,120 Q 470,130 600,366 L0,366 Z" fill="var(--navy)"/>
    </svg>

    <div class="front-brand"><span class="mark-dot"></span><span>VELUNDA</span></div>

    <p class="person"><span class="name">Your Name,</span> <span class="title">Title</span></p>

    <address class="address">Street Name<br>City Name<br>State, City Zip Code</address>
    <span class="divider"></span>

    <ul class="contacts">
      <li>
        <svg viewBox="0 0 16 16" aria-hidden="true"><circle cx="8" cy="8" r="7.5" fill="none" stroke="#fff"/><path d="M5 4.5 L6.6 4.3 L7.2 6.2 L6.3 7 Q7 8.8 8.9 9.7 L9.8 8.8 L11.7 9.4 L11.5 11 Q7.8 11.4 5 7.2 Z" fill="#fff"/></svg>
        010-555-0147
      </li>
      <li>
        <svg viewBox="0 0 16 16" aria-hidden="true"><circle cx="8" cy="8" r="7.5" fill="none" stroke="#fff"/><path d="M5 4.5 L6.6 4.3 L7.2 6.2 L6.3 7 Q7 8.8 8.9 9.7 L9.8 8.8 L11.7 9.4 L11.5 11 Q7.8 11.4 5 7.2 Z" fill="#fff"/></svg>
        010-555-0147
      </li>
      <li>
        <svg viewBox="0 0 16 16" aria-hidden="true"><rect x="1" y="3.5" width="14" height="9" rx="1" fill="#fff"/><path d="M1.5 4 L8 9 L14.5 4" fill="none" stroke="var(--navy)" stroke-width="1.3"/></svg>
        name@velunda.com
      </li>
      <li>
        <svg viewBox="0 0 16 16" aria-hidden="true"><circle cx="8" cy="8" r="7" fill="none" stroke="#fff" stroke-width="1.2"/><ellipse cx="8" cy="8" rx="3" ry="7" fill="none" stroke="#fff" stroke-width="1"/><path d="M1 8 H15 M2.5 4.5 H13.5 M2.5 11.5 H13.5" stroke="#fff" stroke-width="1"/></svg>
        www.velunda.com
      </li>
    </ul>
  </section>

</main>
</body>
</html>
```